Accounting firm needing business card / letterhead designed
Marcus L. Trenholm, CPA
marcus@veltrowledger.com
www.veltrowledger.com
842 E Alder Ave Calvercrest, WA 43827
419-562-0974

```html
<!DOCTYPE html>
<html lang="en">
<head>
<meta charset="utf-8">
<title>Veltrow Ledger — Business Card</title>
<link href="https://fonts.googleapis.com/css2?family=Roboto:wght@400;500&family=Roboto+Condensed:wght@500&display=swap" rel="stylesheet">
<style>
  :root {
    --navy: #241f5e;
    --green: #84bd3a;
    --paper: #f4f4f4;
    --backdrop: #e6e3df;
    --ink-grey: #555555;
    --white: #ffffff;
  }
  * { box-sizing: border-box; margin: 0; padding: 0; }
  html, body { width: 1200px; height: 960px; overflow: hidden; }
  body {
    position: relative;
    background: var(--backdrop);
    font-family: "Roboto", Arial, sans-serif;
  }
  .card {
    position: absolute;
    width: 600px;
    height: 343px;
    background: var(--paper);
    box-shadow: 0 2px 5px rgba(0,0,0,0.35);
    overflow: hidden;
  }
  .card--front { left: 314px; top: 113px; }
  .card--back  { left: 311px; top: 472px; }

  .card__accent {
    position: absolute; left: 0; top: 0;
    width: 100%; height: 15px;
    background: var(--green);
  }
  .brand {
    position: absolute; left: 0; width: 100%;
    text-align: center;
    font-family: "Roboto", Arial, sans-serif;
    font-weight: 500;
    color: var(--navy);
    letter-spacing: 3px;
    white-space: nowrap;
  }
  .card--front .brand { top: 92px; font-size: 46px; }
  .card--back .brand  { top: 132px; font-size: 48px; }

  .contact-band {
    position: absolute; left: 0; bottom: 0;
    width: 100%; height: 122px;
    background: var(--navy);
    color: var(--white);
    text-align: center;
  }
  .contact-band__name {
    margin-top: 24px;
    font-family: "Roboto Condensed", Arial, sans-serif;
    font-weight: 500;
    font-size: 22px;
    color: var(--green);
  }
  .contact-band__line {
    margin-top: 6px;
    font-size: 14.5px;
    display: flex; justify-content: center; align-items: center; gap: 6px;
  }
  .contact-band__item { display: inline-flex; align-items: center; gap: 3px; }
  .contact-band__item svg { width: 12px; height: 12px; fill: var(--green); }
  .contact-band__address { margin-top: 6px; font-size: 14.5px; }

  .card__web {
    position: absolute; left: 0; width: 100%; top: 282px;
    text-align: center;
    font-size: 14px;
    letter-spacing: 8px;
    color: var(--ink-grey);
  }
</style>
</head>
<body>
  <section class="card card--front">
    <div class="card__accent"></div>
    <div class="brand">VELTROW LEDGER</div>
    <div class="contact-band">
      <div class="contact-band__name">Marcus L. Trenholm, CPA</div>
      <div class="contact-band__line">
        <span class="contact-band__item">
          <svg viewBox="0 0 24 24" aria-hidden="true"><path d="M6.6 10.8a15.1 15.1 0 0 0 6.6 6.6l2.2-2.2c.3-.3.7-.4 1-.2 1.1.4 2.3.6 3.6.6.6 0 1 .4 1 1V20c0 .6-.4 1-1 1A17 17 0 0 1 3 4c0-.6.4-1 1-1h3.5c.6 0 1 .4 1 1 0 1.3.2 2.5.6 3.6.1.3 0 .7-.2 1z"/></svg>
          555-562-0974
        </span>
        <span class="contact-band__item">
          <svg viewBox="0 0 24 24" aria-hidden="true"><path d="M2 5h20v14H2z M2 5l10 8 10-8" stroke="#241f5e" stroke-width="1.5"/></svg>
          marcus@veltrowledger.com
        </span>
        <span class="contact-band__item">
          <svg viewBox="0 0 24 24" aria-hidden="true"><circle cx="12" cy="12" r="10"/><path d="M2 12h20M12 2c3 3 3 17 0 20M12 2c-3 3-3 17 0 20" stroke="#241f5e" stroke-width="1.5" fill="none"/></svg>
          www.veltrowledger.com
        </span>
      </div>
      <div class="contact-band__address">842 E Alder Ave, Calvercrest, WA 43827</div>
    </div>
  </section>

  <section class="card card--back">
    <div class="brand">VELTROW LEDGER</div>
    <div class="card__web">www.veltrowledger.com</div>
  </section>
</body>
</html>
```